Quellbrook Market Counsel needs an email sign off and professional power point template

Newly formed company and we require:1. graphic email signature on our email , and2.a professional powerpoint template (title page and sub pages) and revamp of the attached powerpoint presentation I have uploaded our business car design (logo and contact details ) and a current powerpoint template we are currently working with. Also a brief of how we operateOur mantra is Discover, Develop, Deliver.

Target Market(s)

multinationals and mid size SME's requiring help to grown new markets or geographies for their business.

Colors
000000

Requirements
Must have
• the mantra..our phases of engagement around assisting clients is:
• 1. Discover
• 2. Develop
• 3. Deliver
Nice to have
• we differentiate ourselves form consultant by actually executing the plan for them (i.e. is the delivery phase)

```html
<!DOCTYPE html>
<html lang="en">
<head>
<meta charset="utf-8">
<title>Quellbrook Market Counsel – Email Signature</title>
<link rel="stylesheet" href="https://fonts.googleapis.com/css2?family=Montserrat:wght@400;500&display=swap">
<style>
  :root {
    --page: #f4f5f7;
    --navy: #04293b;
    --peak-bright: #1b82a8;
    --peak-mid: #35627c;
    --peak-deep: #2e5774;
    --accent: #1b8bbd;
    --ink-light: #ffffff;
  }
  * { margin: 0; padding: 0; box-sizing: border-box; }
  html, body {
    width: 1199px;
    height: 1200px;
    overflow: hidden;
    background: var(--page);
    font-family: "Montserrat", Arial, sans-serif;
  }
  .signature {
    position: absolute;
    left: 191px;
    top: 450px;
    width: 818px;
    height: 215px;
    background: var(--navy);
    overflow: hidden;
  }
  .signature__art {
    position: absolute;
    left: 0;
    top: 0;
    width: 342px;
    height: 215px;
    background: linear-gradient(100deg, var(--peak-bright) 0%, var(--peak-mid) 45%, var(--peak-deep) 80%, var(--navy) 100%);
  }
  .signature__brand {
    position: absolute;
    left: 220px;
    top: 120px;
    transform: translate(-50%, -50%);
    display: flex;
    align-items: center;
    gap: 7px;
    color: var(--ink-light);
    font-weight: 500;
    font-size: 17px;
    letter-spacing: 0.04em;
  }
  .signature__brand-mark {
    width: 10px;
    height: 10px;
    background: var(--ink-light);
  }
  .signature__company {
    position: absolute;
    left: 355px;
    top: 60px;
    color: var(--ink-light);
    font-weight: 500;
    font-size: 18px;
    line-height: 21px;
    letter-spacing: 0.03em;
    text-transform: uppercase;
  }
  .signature__person {
    position: absolute;
    left: 355px;
    top: 134px;
  }
  .signature__name {
    color: var(--ink-light);
    font-weight: 500;
    font-size: 18px;
    letter-spacing: 0.04em;
    text-transform: uppercase;
    line-height: 22px;
  }
  .signature__role {
    color: var(--accent);
    font-weight: 500;
    font-size: 14px;
    letter-spacing: 0.03em;
    text-transform: uppercase;
    line-height: 18px;
  }
  .signature__contacts {
    position: absolute;
    left: 604px;
    top: 132px;
    list-style: none;
  }
  .contact {
    display: flex;
    align-items: center;
    height: 20.5px;
    color: var(--ink-light);
    font-size: 13px;
  }
  .contact__icon {
    width: 12px;
    height: 12px;
    margin-right: 10px;
    flex: none;
  }
</style>
</head>
<body>
  <section class="signature">
    <div class="signature__art" role="img" aria-label="Layered blue mountain peaks illustration"></div>
    <div class="signature__brand"><span class="signature__brand-mark"></span>Quellbrook</div>

    <h1 class="signature__company">Quellbrook Market<br>Counsel</h1>

    <div class="signature__person">
      <p class="signature__name">Maren&nbsp; Ellsworth</p>
      <p class="signature__role">Principal</p>
    </div>

    <ul class="signature__contacts">
      <li class="contact">
        <svg class="contact__icon" viewBox="0 0 12 12"><path d="M4 1 L2.5 2.5 C1.5 5 4 9 8 10.5 L10 9.5 L8.5 7.5 L7 8.3 C5.5 7.5 4.3 6 3.8 4.6 L5 3.5 Z" fill="var(--accent)"/></svg>
        555-014-2290
      </li>
      <li class="contact">
        <svg class="contact__icon" viewBox="0 0 12 12"><rect x="1" y="3" width="10" height="7" fill="var(--accent)"/><path d="M1 3 L6 7 L11 3" stroke="var(--navy)" stroke-width="1" fill="none"/></svg>
        maren@quellbrook.ca
      </li>
      <li class="contact">
        <svg class="contact__icon" viewBox="0 0 12 12" fill="none" stroke="var(--accent)" stroke-width="1"><circle cx="6" cy="6" r="5"/><ellipse cx="6" cy="6" rx="2.2" ry="5"/><path d="M1 6 H11 M2 3.5 H10 M2 8.5 H10"/></svg>
        www.quellbrook.ca
      </li>
    </ul>
  </section>
</body>
</html>
```